International Manufacturing Business Needs A Heavy Hitting Wordpress Design!

We need wordpress template designs for a new website for our UK based International company Dalvesham Engineering Ltd. We manufacture and supply steel security doors and window units. We would like designs that feature the black and yellow industrial "stripes" that can be seen at our current site www.dalvoportals.com. The final design should communicate strength, power and weight to represent the quality of the products and the security that they provide.

It feels like we need 3 different types of page to be able to be created as per the current website at www.dalvosafeportals.com.

Homepage
Products/Accessories
Leadtimes/Downloads/Contact

It may be that 3 different page types can be created with one template. I'm totally open to this.

I don't like the way that the site currently handles product images, nobody wants to click on even thumbnail to see the product. http://dalvosafeportals.com/products/personnel-doors/

Totally open to suggestions on layout to enable the feeling outlined in the brief above.

Please ask if anything is not clear or you need answers to drill down on specifics.

Sick

Target Market(s)

Businesses that buy steel doors

Font styles to use
Sans Serif
Other font styles liked:
• Copperplate Gothic Bold - For Company Name but we are open to suggestions

Colors

Designer to choose colors to be used in the design.

Requirements
Must have
• Professional looking, clean design
• Conveys strength, power and weight to represent the quality of the products, the characteristics of steel and the security that they provide.
• Incorporates black and yellow stripes of our branding
• Ability to create pages with content as seen at www.dalvosafeportals.com
• A better way of showing the product images
Nice to have
• If possible. a design that gives off the feeling that not only do we supply the products we also make them in house too. I don't know what this looks like but a way of differentiating between a supply only business and one that manufacturers the product too.
Should not have
• We don't like the current thumbnail method of showing the product images

```html
<!DOCTYPE html>
<html lang="en">
<head>
<meta charset="utf-8">
<title>Dalvesham Engineering Ltd – Security &amp; Fire Exit Doors</title>
<link href="https://fonts.googleapis.com/css2?family=Marcellus&family=Open+Sans:wght@400;600;700&display=swap" rel="stylesheet">
<style>
:root{
  --yellow:#f2e500;
  --olive:#8f8a1e;
  --ink:#1b1b1b;
  --dark:#202020;
  --text:#555;
  --teal:#4b8f97;
  --teal-light:#dff3f5;
  --yellow-light:#fbfbdc;
  --white:#fff;
  --head:"Marcellus", serif;
  --body:"Open Sans", sans-serif;
}
*{box-sizing:border-box;margin:0;padding:0}
html,body{width:1200px;height:2715px;overflow:hidden;background:var(--white)}
body{position:relative;font-family:var(--body);color:var(--text)}
.abs{position:absolute}

/* header */
.site-header{left:0;top:0;width:1200px;height:125px;background:var(--dark);border-top:5px solid var(--yellow)}
.brand{display:flex;align-items:center;gap:12px;color:var(--white);font-family:var(--head);font-size:24px;line-height:1.05;letter-spacing:1px}
.brand-mark{width:34px;height:34px;background:var(--teal);flex:none}
.site-header .brand{left:100px;top:32px}
.contact-bar{right:100px;top:32px;display:flex;gap:18px;color:var(--white);font-size:13px;align-items:center}
.contact-bar svg{vertical-align:-2px;margin-right:8px}
.main-nav{right:100px;top:80px;display:flex;gap:26px;font-size:13px;font-weight:700;color:var(--white);letter-spacing:.2px}
.main-nav .active{color:var(--yellow)}

/* hero */
.hero{left:0;top:125px;width:1200px;height:550px;background:linear-gradient(120deg,#3a3a2a 0%,#6b6a3a 35%,#8c8a3c 60%,#3e3d2b 100%);overflow:hidden}
.hero-slash{left:0;top:0;width:1200px;height:550px}
.hero-title{left:0;width:1200px;top:108px;text-align:center;font-family:var(--head);font-size:38px;color:var(--white);letter-spacing:1px}
.hero-split{left:0;top:215px;width:1200px;height:160px}
.hero-label{top:255px;font-family:var(--head);font-size:25px;color:var(--white)}
.hero-btn{left:495px;top:375px;width:210px;height:44px;border-radius:22px;background:var(--teal);color:var(--white);font-weight:700;font-size:15px;text-align:center;line-height:44px}
.hero-dots{left:1146px;top:236px;display:flex;flex-direction:column;gap:18px}
.hero-dots span{width:15px;height:15px;border:2px solid var(--white);border-radius:50%}
.hero-dots .on{background:var(--white)}

/* what we do */
.about{left:0;top:675px;width:1200px;height:522px;background:#f7f7f7}
.about-ghost{left:-120px;top:240px;transform:rotate(-90deg);font-family:var(--head);font-size:64px;color:#ececec;white-space:nowrap}
.section-title{font-family:var(--head);font-size:30px;color:var(--ink)}
.about .section-title{left:98px;top:88px}
.about-list{left:98px;top:150px;width:500px;list-style:none;font-size:12.5px;line-height:1.45;color:#555}
.about-list li{position:relative;padding-left:26px;margin-bottom:14px}
.about-list svg{position:absolute;left:0;top:2px}
.video{left:640px;top:95px;width:460px;height:345px;border:4px solid var(--white);box-shadow:0 2px 8px rgba(0,0,0,.2);background:linear-gradient(135deg,#8e9294,#5d6265 55%,#c7cacb)}
.video-play{left:198px;top:141px}

/* band */
.stripe-band{left:0;top:1197px;width:1200px;height:128px;background:linear-gradient(90deg,#1c1c1c 0%,#5a5614 30%,#a39c1c 55%,#5a5614 80%,#1c1c1c 100%)}
.band-title{top:48px;font-family:var(--head);font-size:30px;color:var(--white)}

/* products */
.products{left:0;top:1325px;width:1200px;height:525px}
.products-security{left:0;top:0;width:600px;height:525px;background:var(--yellow-light)}
.products-fire{left:600px;top:0;width:600px;height:525px;background:var(--teal-light)}
.product-card{width:245px;height:210px}
.product-photo{width:245px;height:165px;background:linear-gradient(135deg,#9a9a9a,#4a4a4a)}
.product-label{height:45px;line-height:45px;text-align:center;font-size:13.5px;font-weight:700;color:var(--ink)}
.products-security .product-label{background:var(--yellow)}
.products-fire .product-label{background:var(--teal);color:#1e1e1e}

/* why choose */
.why{left:0;top:1850px;width:1200px;height:502px;background:#fafafa}
.why-ghost{left:0;width:1200px;top:70px;text-align:center;font-family:var(--head);font-size:48px;color:#ececec}
.why .section-title{left:0;width:1200px;top:87px;text-align:center;font-size:32px}
.why-intro{left:260px;width:680px;top:153px;text-align:center;font-size:12px;line-height:2}
.feature{width:240px;text-align:center}
.feature svg{display:block;margin:0 auto}
.feature h3{margin-top:22px;font-size:16px;font-weight:600;color:var(--ink)}
.feature p{margin-top:10px;font-size:11.5px;line-height:2;color:#666}
.why-arrow{top:318px}

/* footer */
.site-footer{left:0;top:2352px;width:1200px;height:363px;background:linear-gradient(#262626,#161616)}
.site-footer .brand{left:98px;top:62px;font-size:26px}
.footer-about{left:98px;top:140px;width:305px;font-size:12.5px;line-height:1.75;color:var(--white);text-align:justify}
.footer-title{top:82px;font-family:var(--head);font-size:16px;color:var(--white);letter-spacing:.5px}
.email-field{left:540px;top:142px;width:297px;height:38px;border:1px solid #bbb;color:var(--white);font-size:13px;padding:0 12px;display:flex;align-items:center;justify-content:space-between}
.subscribe-btn{left:540px;top:193px;width:125px;height:38px;background:var(--yellow);color:var(--ink);font-weight:700;font-size:14px;text-align:center;line-height:38px}
.social{left:948px;top:138px;display:flex;gap:10px}
.social-link{width:44px;height:44px;border-radius:50%;background:var(--white);display:flex;align-items:center;justify-content:center}
.footer-band{left:0;top:262px;width:1200px;height:40px;background:linear-gradient(90deg,#2a2812,#4a4720 50%,#2a2812)}
.footer-rule{left:98px;top:290px;width:1004px;height:1px;background:#777}
.copyright{left:0;width:1200px;top:317px;text-align:center;font-size:13px;color:var(--white)}
</style>
</head>
<body>

<header class="site-header abs">
  <div class="brand abs"><span class="brand-mark"></span><span>DALVESHAM<br>ENGINEERING LTD.</span></div>
  <div class="contact-bar abs">
    <span><svg width="12" height="12" viewBox="0 0 24 24"><path fill="#f2e500" d="M6.6 10.8a15 15 0 0 0 6.6 6.6l2.2-2.2c.3-.3.7-.4 1-.2 1.1.4 2.3.6 3.6.6.6 0 1 .4 1 1V20c0 .6-.4 1-1 1A17 17 0 0 1 3 4c0-.6.4-1 1-1h3.5c.6 0 1 .4 1 1 0 1.3.2 2.5.6 3.6.1.3 0 .7-.2 1z"/></svg>+44 (0)1632 960 418</span>
    <span>|</span>
    <span><svg width="13" height="11" viewBox="0 0 26 20"><rect width="26" height="20" rx="2" fill="#f2e500"/><path d="M1 2l12 9 12-9" stroke="#202020" stroke-width="2" fill="none"/></svg>sales@dalvoportals.com</span>
  </div>
  <nav class="main-nav abs">
    <span class="active">HOME</span><span>PRODUCTS</span><span>ACCESSORIES</span><span>DELIVERY &amp; LEAD TIMES</span><span>DOWNLOADS</span><span>CONTACT</span>
  </nav>
</header>

<section class="hero abs" role="img" aria-label="Photo of a glass entrance with a security keypad and plants, tinted yellow">
  <svg class="hero-slash abs" viewBox="0 0 1200 550"><polygon points="330,0 560,0 230,550 0,550 0,440" fill="rgba(0,0,0,.35)"/><polygon points="820,0 1200,0 1200,90 960,550 640,550" fill="rgba(242,229,0,.18)"/></svg>
  <h1 class="hero-title abs">OUR SUPERIOR QUALITY &amp; RELIABILITY</h1>
  <svg class="hero-split abs" viewBox="0 0 1200 160"><line x1="510" y1="57" x2="545" y2="57" stroke="#fff" stroke-width="2"/><line x1="655" y1="57" x2="690" y2="57" stroke="#fff" stroke-width="2"/><line x1="600" y1="114" x2="600" y2="150" stroke="#fff" stroke-width="2"/><circle cx="600" cy="57" r="57" fill="#fff"/><rect x="580" y="30" width="40" height="54" fill="#4b8f97"/></svg>
  <div class="hero-label abs" style="left:296px">SECURITY DOORS</div>
  <div class="hero-label abs" style="left:715px">FIRE EXIT DOORS</div>
  <div class="hero-btn abs">GET STARTED NOW</div>
  <div class="hero-dots abs"><span></span><span class="on"></span><span></span></div>
</section>

<section class="about abs">
  <div class="about-ghost abs">WHAT WE DO</div>
  <h2 class="section-title abs">WHAT WE DO</h2>
  <ul class="about-list abs">
    <li><svg width="12" height="12" viewBox="0 0 12 12"><circle cx="4" cy="4" r="3" fill="none" stroke="#e0d400" stroke-width="1.6"/><path d="M6 6l5 5" stroke="#e0d400" stroke-width="1.6"/></svg>Dalvesham security doors combine a high level of security with exceptional value.</li>
    <li><svg width="12" height="12" viewBox="0 0 12 12"><circle cx="4" cy="4" r="3" fill="none" stroke="#e0d400" stroke-width="1.6"/><path d="M6 6l5 5" stroke="#e0d400" stroke-width="1.6"/></svg>Our superior quality and proven reliability has made us the first choice for a wide range of companies no matter what their requirement or application.</li>
    <li><svg width="12" height="12" viewBox="0 0 12 12"><circle cx="4" cy="4" r="3" fill="none" stroke="#e0d400" stroke-width="1.6"/><path d="M6 6l5 5" stroke="#e0d400" stroke-width="1.6"/></svg>All of our products are designed and manufactured to the highest specification, combine this with a rigorous quality control system and an extensive after-sales service and it is easy to see why we are seen as industry leaders.</li>
    <li><svg width="12" height="12" viewBox="0 0 12 12"><circle cx="4" cy="4" r="3" fill="none" stroke="#e0d400" stroke-width="1.6"/><path d="M6 6l5 5" stroke="#e0d400" stroke-width="1.6"/></svg>We place particular emphasis on continuous development and twelve years experience ensures that we are always ahead of the competition and that we can react quickly to customer's requirements.</li>
    <li><svg width="12" height="12" viewBox="0 0 12 12"><circle cx="4" cy="4" r="3" fill="none" stroke="#e0d400" stroke-width="1.6"/><path d="M6 6l5 5" stroke="#e0d400" stroke-width="1.6"/></svg>Each and every Dalvesham product is subject to our fifty point quality control process before it is dispatched.</li>
    <li><svg width="12" height="12" viewBox="0 0 12 12"><circle cx="4" cy="4" r="3" fill="none" stroke="#e0d400" stroke-width="1.6"/><path d="M6 6l5 5" stroke="#e0d400" stroke-width="1.6"/></svg>Dalvesham have forged a reputation for affordable, high quality steel doors.</li>
  </ul>
  <div class="video abs" role="img" aria-label="Video still of a man in a suit using a door access keypad">
    <svg class="video-play abs" width="56" height="56" viewBox="0 0 56 56"><circle cx="28" cy="28" r="28" fill="rgba(255,255,255,.9)"/><polygon points="22,17 40,28 22,39" fill="#1b1b1b"/></svg>
  </div>
</section>

<section class="stripe-band abs" role="img" aria-label="Black and yellow hazard stripe banner">
  <h2 class="band-title abs" style="left:98px">SECURITY DOORS</h2>
  <h2 class="band-title abs" style="right:98px">FIRE EXIT DOORS</h2>
</section>

<section class="products abs">
  <div class="products-security abs">
    <div class="product-card abs" style="left:45px;top:41px"><div class="product-photo" role="img" aria-label="Steel vault door with round locking wheel"></div><div class="product-label">ANTI-VANDAL STEEL CABINS</div></div>
    <div class="product-card abs" style="left:320px;top:41px"><div class="product-photo" role="img" aria-label="Dark door in a white modular building" style="background:linear-gradient(135deg,#e6e6e6,#5a5a5a)"></div><div class="product-label">MODULAR BUILDINGS</div></div>
    <div class="product-card abs" style="left:45px;top:278px"><div class="product-photo" role="img" aria-label="Door lever handle on a dark steel door" style="background:linear-gradient(135deg,#8b7763,#2a2a2a)"></div><div class="product-label">STEEL FRAMED BUILDINGS</div></div>
    <div class="product-card abs" style="left:320px;top:278px"><div class="product-photo" role="img" aria-label="Chrome lever handle and lock" style="background:linear-gradient(135deg,#c9c9c9,#7d7d7d)"></div><div class="product-label">GLAZING UNIT</div></div>
  </div>
  <div class="products-fire abs">
    <div class="product-card abs" style="left:33px;top:41px"><div class="product-photo" role="img" aria-label="White lever handle on a dark door" style="background:linear-gradient(135deg,#7a8288,#2c2f31)"></div><div class="product-label">BLANK DOORS</div></div>
    <div class="product-card abs" style="left:307px;top:41px"><div class="product-photo" role="img" aria-label="Red framed glazed doors" style="background:linear-gradient(135deg,#c8202a,#7a1015)"></div><div class="product-label">ACOUSTIC DOORS</div></div>
    <div class="product-card abs" style="left:33px;top:278px"><div class="product-photo" role="img" aria-label="Door handle with multi-point lock on wooden door" style="background:linear-gradient(135deg,#c7a472,#6b5437)"></div><div class="product-label">ANTI - VANDAL STEEL</div></div>
    <div class="product-card abs" style="left:307px;top:278px"><div class="product-photo" role="img" aria-label="Open blue steel vault door" style="background:linear-gradient(135deg,#5b7fa8,#3a3a3a)"></div><div class="product-label">STEEL FRAMED DOORS</div></div>
  </div>
</section>

<section class="why abs">
  <div class="why-ghost abs">WHY CHOOSE US</div>
  <h2 class="section-title abs">WHY CHOOSE US?</h2>
  <p class="why-intro abs">Nemo enim ipsam voluptatem quia voluptas sit aspernatur aut odit aut fugit, sed quia consequuntur magni dolores eos qui ratione voluptatem sequi nesciunt. Neque porro quisquam est, qui dolorem ipsum quia dolor sit amet</p>
  <svg class="why-arrow abs" style="left:44px" width="12" height="20" viewBox="0 0 12 20"><path d="M10 2L2 10l8 8" stroke="#999" stroke-width="2" fill="none"/></svg>
  <svg class="why-arrow abs" style="left:1144px" width="12" height="20" viewBox="0 0 12 20"><path d="M2 2l8 8-8 8" stroke="#999" stroke-width="2" fill="none"/></svg>

  <div class="feature abs" style="left:92px;top:245px">
    <svg width="80" height="64" viewBox="0 0 80 64"><rect x="28" y="26" width="24" height="20" rx="2" fill="#f2e500" stroke="#222" stroke-width="2"/><path d="M33 26v-6a7 7 0 0 1 14 0v6" fill="none" stroke="#222" stroke-width="2"/><path d="M28 36H10v-16M52 36h18v-16M40 46v14" stroke="#222" stroke-width="2" fill="none"/><circle cx="10" cy="16" r="4" fill="none" stroke="#222" stroke-width="2"/><circle cx="70" cy="16" r="4" fill="none" stroke="#222" stroke-width="2"/></svg>
    <h3>HIGH LEVEL SECURITY</h3>
    <p>Nemo enim ipsam voluptatem quia voluptas sit aspernatur aut odit aut fugit</p>
  </div>
  <div class="feature abs" style="left:351px;top:245px">
    <svg width="80" height="64" viewBox="0 0 80 64"><path d="M14 52l30-14 22 8-30 14z" fill="none" stroke="#222" stroke-width="2"/><path d="M20 40l30-14 16 6-30 14z" fill="#f2e500" stroke="#222" stroke-width="2"/><path d="M26 28l30-14 12 4-30 14z" fill="none" stroke="#222" stroke-width="2"/></svg>
    <h3>HIGH QUALITY STEEL</h3>
    <p>Nemo enim ipsam voluptatem quia voluptas sit aspernatur aut odit aut fugit</p>
  </div>
  <div class="feature abs" style="left:610px;top:245px">
    <svg width="80" height="64" viewBox="0 0 80 64"><path d="M10 26L40 6l30 20v34H10z" fill="none" stroke="#222" stroke-width="2"/><rect x="30" y="28" width="20" height="14" fill="#f2e500" stroke="#222" stroke-width="2"/><rect x="16" y="44" width="22" height="12" fill="none" stroke="#222" stroke-width="2"/><rect x="42" y="44" width="22" height="12" fill="none" stroke="#222" stroke-width="2"/></svg>
    <h3>5000 UNITS IN STOCK</h3>
    <p>Nemo enim ipsam voluptatem quia voluptas sit aspernatur aut odit aut fugit</p>
  </div>
  <div class="feature abs" style="left:868px;top:245px">
    <svg width="80" height="64" viewBox="0 0 80 64"><circle cx="34" cy="18" r="12" fill="none" stroke="#222" stroke-width="2"/><path d="M34 10v8h6" stroke="#222" stroke-width="2" fill="none"/><rect x="14" y="32" width="34" height="20" fill="#f2e500" stroke="#222" stroke-width="2"/><path d="M48 38h12l8 8v6H48" fill="none" stroke="#222" stroke-width="2"/><circle cx="24" cy="55" r="4" fill="#fff" stroke="#222" stroke-width="2"/><circle cx="58" cy="55" r="4" fill="#fff" stroke="#222" stroke-width="2"/></svg>
    <h3>DELIVERY &amp; TIMES</h3>
    <p>Nemo enim ipsam voluptatem quia voluptas sit aspernatur aut odit aut fugit</p>
  </div>
</section>

<footer class="site-footer abs">
  <div class="brand abs"><span class="brand-mark"></span><span>DALVESHAM<br>ENGINEERING LTD.</span></div>
  <p class="footer-about abs">Nemo enim ipsam voluptatem quia voluptas sit aspernatur aut odit aut fugit, sed quia consequuntur magni dolores eos qui ratione voluptatem sequi nesciunt. Neque porro quisquam...</p>
  <h4 class="footer-title abs" style="left:540px">NEWSLETTER SUBSCRIBE</h4>
  <div class="email-field abs"><span>Enter Email</span><svg width="14" height="11" viewBox="0 0 26 20"><rect width="26" height="20" rx="2" fill="#fff"/><path d="M1 2l12 9 12-9" stroke="#202020" stroke-width="2" fill="none"/></svg></div>
  <div class="subscribe-btn abs">SUBSCRIBE</div>
  <h4 class="footer-title abs" style="left:948px">FOLLOW US ON</h4>
  <div class="social abs">
    <span class="social-link" role="img" aria-label="Social profile link"><svg width="18" height="18" viewBox="0 0 24 24"><circle cx="6" cy="12" r="3" fill="#2b5fa8"/><circle cx="18" cy="5" r="3" fill="#2b5fa8"/><circle cx="18" cy="19" r="3" fill="#2b5fa8"/><path d="M6 12L18 5M6 12l12 7" stroke="#2b5fa8" stroke-width="2"/></svg></span>
    <span class="social-link" role="img" aria-label="Social profile link"><svg width="18" height="18" viewBox="0 0 24 24"><circle cx="6" cy="12" r="3" fill="#2a9ad6"/><circle cx="18" cy="5" r="3" fill="#2a9ad6"/><circle cx="18" cy="19" r="3" fill="#2a9ad6"/><path d="M6 12L18 5M6 12l12 7" stroke="#2a9ad6" stroke-width="2"/></svg></span>
    <span class="social-link" role="img" aria-label="Social profile link"><svg width="18" height="18" viewBox="0 0 24 24"><circle cx="6" cy="12" r="3" fill="#c8237e"/><circle cx="18" cy="5" r="3" fill="#c8237e"/><circle cx="18" cy="19" r="3" fill="#c8237e"/><path d="M6 12L18 5M6 12l12 7" stroke="#c8237e" stroke-width="2"/></svg></span>
  </div>
  <div class="footer-band abs" role="img" aria-label="Faint hazard stripe strip"></div>
  <div class="footer-rule abs"></div>
  <p class="copyright abs">© Copyright 2018 Dalvesham Engineering. All Rights Reserved &nbsp; | &nbsp; Privacy Policy.</p>
</footer>

</body>
</html>
```